Wordpress Design (uncoded) Auction & Real Estate 3 in 1

This will be an uncoded Wordpress theme design only. Winning designer will provide PSD source files.

We need a wordpress themedesign for an established auction and real estate company based in Pennsylvania. The client wants one overall theme for their primary company website with 2 child themes, one for auction division and one for real estate division. Each child theme will have it's own color scheme and some variation in layout.

The primary company logo is Blue with white/black/silver elements. (see attached zip file)

The auction division logo is Gold with black/white elements (see attached zip file)

The real estate division logo is Green with white/black/silver elements. (see attached zip file)

Also attached are 2 PDF files showing a sample layout that the client came up with that they really like; however, this should only be used as a starting point. We want to see what creative, clean layouts you can come up with.

Industry/Entity Type

Real Estate

Requirements
Must have
• - We will require winning designer to provide a layered PSD (Adobe photoshop) concept files, along with any non-standard font files used.

A slideshow element on the home page using the placeholder image provided.

Primary Site navigation for merrowtonhalvecompanies.example:

Home
Services
-Auctions/Appraisals
-Real Estate Auctions
-Real Estate Listings
About Us
-History
-Auction Center
Contact Us

Secondary site - halvegavelhouse.example navigation:
Home
Auctions
Buy/Sell
Collections
Services
Contact Us

Secondary site - merrowtonhalve.example
Home
Properties
Real Estate Auctions
Buying
Selling
Area Info
About Us
Contact Us
Nice to have
• Sidebar widgets: Email sign-up form - Featured Auctions - Featured Assets for Sale

```html
<!DOCTYPE html>
<html lang="en">
<head>
<meta charset="utf-8">
<title>Halve Gavel House – Auction &amp; Appraisal</title>
<link rel="stylesheet" href="https://fonts.googleapis.com/css2?family=Arimo:wght@400;700&family=Philosopher&family=Crimson+Text&display=swap">
<style>
:root{
  --page:#e4e4e4;
  --ink:#222;
  --brown:#5a4a36;
  --brown-dark:#3a2e25;
  --gold-hi:#c9b089;
  --gold:#b39869;
  --gold-lo:#9a7f54;
  --panel:#2c2a29;
  --panel-hi:#4a4644;
  --footer:#3d3532;
  --footer-bar:#2a2422;
  --footer-text:#d8d2cc;
  --white:#fff;
}
*{box-sizing:border-box;margin:0;padding:0}
html,body{width:1115px;height:1200px;overflow:hidden}
body{position:relative;background:radial-gradient(ellipse 480px 260px at 290px 90px,#f6f6f6,var(--page) 70%);font-family:"Arimo",Arial,sans-serif;color:var(--ink);border-top:3px solid #4a4444}
.abs{position:absolute}

/* header */
.brand{left:123px;top:30px;display:flex;align-items:center;gap:10px}
.brand-dot{width:62px;height:62px;border-radius:50%;background:var(--brown-dark)}
.brand-name{font-family:"Philosopher",sans-serif;font-size:30px;color:var(--brown-dark);line-height:1}
.search{left:800px;top:50px;width:204px;height:30px;background:var(--white);border:1px solid #d6d6d6;display:flex;align-items:center;justify-content:space-between;padding:0 8px;font-size:13px;color:#aaa}

/* nav */
.nav{left:123px;top:135px;width:880px;height:42px;border-radius:6px;background:linear-gradient(var(--gold-hi),var(--gold) 55%,var(--gold-lo));box-shadow:0 1px 2px rgba(0,0,0,.3)}
.nav-item{position:absolute;top:0;height:42px;line-height:42px;color:var(--white);font-size:13px;text-transform:uppercase}
.nav-sep{position:absolute;top:8px;width:1px;height:26px;background:rgba(255,255,255,.45)}
.nav-home{left:14px;top:6px;width:73px;height:43px;line-height:33px;text-align:center;background:linear-gradient(#4a4444,#222);border-radius:4px 4px 0 0}

/* hero */
.hero{left:121px;top:191px;width:881px;height:335px;background:var(--white);box-shadow:0 6px 8px -4px rgba(0,0,0,.25)}
.hero-photo{left:7px;top:10px;width:614px;height:317px;background:linear-gradient(180deg,#c4a58a 0%,#d8cbb0 30%,#8a6b4d 60%,#2d2620 100%)}
.signup{left:622px;top:10px;width:248px;height:317px;background:linear-gradient(var(--panel-hi),var(--panel) 60%,#222)}
.signup-head{left:11px;top:12px;width:244px;height:43px;background:linear-gradient(var(--gold-hi),var(--gold-lo));border-radius:4px 0 0 4px;color:var(--white);font-family:"Crimson Text",serif;font-size:21px;line-height:43px;padding-left:13px}
.field{left:17px;width:213px;height:30px;background:var(--white);border:1px solid #999;font-size:12px;color:#555;line-height:28px;padding-left:7px}
.signup-btn{left:16px;top:246px;width:118px;height:36px;border-radius:6px;background:linear-gradient(var(--gold-hi),var(--gold-lo));color:var(--white);font-family:"Crimson Text",serif;font-size:18px;display:flex;align-items:center;justify-content:center;gap:9px}

/* content */
.content{left:122px;top:557px;width:877px;height:474px;background:var(--white)}
.ribbon{position:absolute;height:33px;line-height:33px;border-radius:0 8px 8px 0;background:linear-gradient(var(--gold-hi),var(--gold-lo));color:var(--white);font-family:"Philosopher",sans-serif;font-size:19px;padding-left:11px;box-shadow:1px 1px 2px rgba(0,0,0,.25)}
.dotted-rail{left:17px;top:48px;height:412px;border-left:1px dotted #bbb}
.listing{position:absolute;left:29px;width:586px;height:180px}
.thumb{position:absolute;left:0;top:0;width:102px;height:77px;border:1px solid #ddd;background:linear-gradient(#9ab3d8,#cfd6dc 45%,#4f8a3b 60%,#3f7330)}
.btn{position:absolute;left:1px;width:102px;height:28px;border-radius:5px;color:var(--white);font-size:13px;font-weight:700;display:flex;align-items:center;gap:9px;padding-left:12px}
.btn-details{top:88px;background:linear-gradient(var(--gold-hi),var(--gold-lo))}
.btn-photos{top:124px;background:linear-gradient(#4a4545,#1c1a1a)}
.listing-title{position:absolute;left:113px;top:12px;font-size:13.5px;font-weight:700;letter-spacing:.8px;color:var(--brown)}
.meta{position:absolute;left:113px;font-size:12px}
.meta b{margin-right:5px}
.desc{position:absolute;left:112px;top:86px;width:460px;font-size:11.6px;line-height:16.7px;text-align:justify}
.divider{left:29px;top:231px;width:578px;border-top:1px dotted #bbb}
.col-right-rail{left:618px;top:48px;height:412px;border-left:1px dotted #ccc}
.feat-link{left:634px;top:64px;font-size:12px;letter-spacing:.6px;color:var(--gold-lo);text-decoration:underline}
.feat-img{border:2px solid #ddd}
.small{font-size:11.6px;line-height:14px}
.read-more{width:68px;height:18px;border-radius:4px;background:#2a0f0d;color:var(--white);font-size:11px;font-style:italic;font-weight:700;text-align:center;line-height:18px}

/* footer */
.footer-rule{left:0;top:1066px;width:1115px;height:5px;background:var(--gold)}
.footer{left:0;top:1071px;width:1115px;height:107px;background:var(--footer)}
.footer-brand{left:160px;top:28px;display:flex;align-items:center;gap:8px;color:var(--white);font-family:"Philosopher",sans-serif;font-size:15px;line-height:1.1}
.footer-brand span{width:26px;height:26px;border-radius:50%;border:2px solid var(--white)}
.fcol{position:absolute;top:26px;color:var(--white)}
.fcol h4{font-weight:400;font-size:13.5px;margin-bottom:8px}
.fcol li{list-style:none;font-size:11.6px;color:var(--footer-text);margin-bottom:5px}
.fcol li::before{content:"»";margin-right:4px;font-size:10px}
.footer-bar{left:0;top:1178px;width:1115px;height:22px;background:var(--footer-bar);color:var(--footer-text);font-size:11.6px;line-height:22px}
</style>
</head>
<body>

<header>
  <div class="abs brand"><div class="brand-dot"></div><div class="brand-name">Halve Gavel House</div></div>
  <div class="abs search">search
    <svg width="16" height="16" viewBox="0 0 16 16"><circle cx="6.5" cy="6.5" r="4.8" fill="none" stroke="#b39869" stroke-width="2.4"/><line x1="10" y1="10" x2="14.5" y2="14.5" stroke="#b39869" stroke-width="2.8" stroke-linecap="round"/></svg>
  </div>
  <nav class="abs nav">
    <div class="nav-item nav-home">HOME</div>
    <div class="nav-sep" style="left:99px"></div>
    <div class="nav-item" style="left:131px">About Us</div>
    <div class="nav-sep" style="left:223px"></div>
    <div class="nav-item" style="left:255px">History</div>
    <div class="nav-sep" style="left:341px"></div>
    <div class="nav-item" style="left:371px">Auction Center</div>
    <div class="nav-sep" style="left:512px"></div>
    <div class="nav-item" style="left:543px">Contact Us</div>
  </nav>
</header>

<section class="abs hero">
  <div class="abs hero-photo" role="img" aria-label="Slideshow photo: auctioneers presenting a framed painting to a seated crowd in a gallery"></div>
  <div class="abs signup">
    <div class="abs signup-head">EMAIL SIGN-UP FORM</div>
    <div class="abs field" style="top:83px">First Name</div>
    <div class="abs field" style="top:138px">Last Name</div>
    <div class="abs field" style="top:192px">Email Address</div>
    <div class="abs signup-btn">SIGN UP
      <svg width="20" height="18" viewBox="0 0 20 18"><path d="M11 2H2v14h9" fill="none" stroke="#3a2e25" stroke-width="2.5"/><path d="M8 9h10M14 5l4 4-4 4" fill="none" stroke="#3a2e25" stroke-width="2.5"/></svg>
    </div>
  </div>
</section>

<main class="abs content">
  <div class="ribbon" style="left:16px;top:15px;width:439px">Shop Equipment/tools * Pork Processing Items</div>
  <div class="abs dotted-rail"></div>

  <article class="listing" style="top:64px">
    <div class="thumb" role="img" aria-label="Auction crowd on a lawn in front of a farmhouse"></div>
    <div class="btn btn-details"><svg width="24" height="11" viewBox="0 0 24 11"><rect width="10" height="11" rx="2" fill="#fff"/><rect x="13" y="1" width="11" height="2" fill="#fff"/><rect x="13" y="5" width="11" height="2" fill="#fff"/><rect x="13" y="9" width="11" height="2" fill="#fff"/></svg>Details</div>
    <div class="btn btn-photos"><svg width="20" height="16" viewBox="0 0 20 16"><rect x="1" y="1" width="14" height="11" fill="none" stroke="#fff" stroke-width="1.6"/><rect x="5" y="4" width="14" height="11" fill="#fff"/></svg>Photos</div>
    <div class="listing-title">LIVE ON-SITE AUCTION</div>
    <div class="meta" style="top:34px"><b>Begins:</b> Saturday, March 16, 2013 at 10:00 AM EDT</div>
    <div class="meta" style="top:54px"><b>Location:</b> 1820 Linden Road Ashford, KY 40100</div>
    <p class="desc">Corvane QX7 High Lift, simply dummy text of the printing and typesetting industry simply dummy text of the printing and typesetting industry 600 Series Tollard tractor w/Brannick Loader, Dune buggy, 1207 TL Cutditioner: SHOP &amp; MISCELLANIOUS &amp; PORK PROCESSING ITEMS.</p>
  </article>

  <div class="abs divider"></div>

  <article class="listing" style="top:249px">
    <div class="thumb" role="img" aria-label="Auction crowd on a lawn in front of a farmhouse"></div>
    <div class="btn btn-details"><svg width="24" height="11" viewBox="0 0 24 11"><rect width="10" height="11" rx="2" fill="#fff"/><rect x="13" y="1" width="11" height="2" fill="#fff"/><rect x="13" y="5" width="11" height="2" fill="#fff"/><rect x="13" y="9" width="11" height="2" fill="#fff"/></svg>Details</div>
    <div class="btn btn-photos"><svg width="20" height="16" viewBox="0 0 20 16"><rect x="1" y="1" width="14" height="11" fill="none" stroke="#fff" stroke-width="1.6"/><rect x="5" y="4" width="14" height="11" fill="#fff"/></svg>Photos</div>
    <div class="listing-title">LIVE ON-SITE AUCTION</div>
    <div class="meta" style="top:34px"><b>Begins:</b> Saturday, March 16, 2013 at 10:00 AM EDT</div>
    <div class="meta" style="top:54px"><b>Location:</b> 1820 Linden Road Ashford, KY 40100</div>
    <p class="desc">Corvane QX7 High Lift, simply dummy text of the printing and typesetting industry simply dummy text of the printing and typesetting industry 600 Series Tollard tractor w/Brannick Loader, Dune buggy, 1207 TL Cutditioner: SHOP &amp; MISCELLANIOUS &amp; PORK PROCESSING ITEMS.</p>
  </article>

  <div class="abs col-right-rail"></div>
  <aside>
    <div class="ribbon" style="left:621px;top:15px;width:214px;padding-left:24px">Featured Auctions</div>
    <div class="abs feat-link">TRACTOR * HI LIFT * MACHINERY</div>
    <div class="abs feat-img" style="left:643px;top:79px;width:148px;height:72px;background:linear-gradient(#9fb7d4,#d9c7b0 45%,#5d8a3e 70%,#4b7430)" role="img" aria-label="Villa with palm trees and lawn"></div>
    <p class="abs small" style="left:635px;top:169px;width:230px"><b>Saturday</b> March 16, 2013 at 10:00 AM</p>
    <p class="abs small" style="left:635px;top:186px;width:220px">simply dummy text of the printing and typesetting industry.</p>
    <div class="abs read-more" style="left:635px;top:218px">read more</div>

    <div class="ribbon" style="left:621px;top:263px;width:230px;padding-left:14px">Featured Assets for Sale</div>
    <div class="abs feat-img" style="left:636px;top:309px;width:196px;height:83px;background:linear-gradient(#c9b8a8,#7a6a5c 50%,#2f2a28)" role="img" aria-label="Auctioneers in suits calling bids outdoors"></div>
    <p class="abs small" style="left:637px;top:400px;width:220px">simply dummy text of the printing and type setting industry dummy text of the printing and type.</p>
    <div class="abs read-more" style="left:635px;top:449px">read more</div>
  </aside>
</main>

<footer>
  <div class="abs footer-rule"></div>
  <div class="abs footer">
    <div class="abs footer-brand"><span></span>Merrowton<br>Halve</div>
    <div class="fcol" style="left:320px"><h4>HOME</h4></div>
    <div class="fcol" style="left:419px"><h4>SERVICES</h4><ul><li>Auction</li><li>Real Estate</li><li>TRAVERSE</li></ul></div>
    <div class="fcol" style="left:543px"><h4>ABOUT US</h4><ul><li>History</li><li>Auction Center</li></ul></div>
    <div class="fcol" style="left:670px"><h4>CONTACT US</h4><ul><li>Privacy</li></ul></div>
  </div>
  <div class="abs footer-bar">
    <span class="abs" style="left:173px">215 555 0142</span>
    <span class="abs" style="left:284px">88 Meadowgate Road , Brookvale, PA 19000</span>
    <span class="abs" style="right:111px">(C) 2013 The Merrowton Halve Companies</span>
  </div>
</footer>

</body>
</html>
```